Storm Restoration Contractor needs a professional letterhead design

Looking for a professional letterhead design. Not looking for your cheapo MS Word standard ones that are readily available. Dont want it to be cookie cutter look like ones readily available online. We just recently changed our logo and want to freshen up all our documents. Our company handles restoring a property back to a pre-loss condition after a storm damages it. For example, wind, hail, flood, fire losses.

Target Market(s)

Property Owners, Homeowners, Property Owners, Commercial Property Owners, Property Management Companies

Industry/Entity Type

Construction Company

Requirements
Must have
• Professional, Use 1 of 2 logo options
• Storm Restoration, Roofing, Siding, Windows

```html
<!DOCTYPE html>
<html lang="en">
<head>
<meta charset="utf-8">
<title>Northgate Exteriors Letterhead</title>
<link href="https://fonts.googleapis.com/css2?family=Open+Sans:wght@400;600;700&display=swap" rel="stylesheet">
<style>
  :root {
    --brand-blue: #1673c4;
    --brand-grey: #4a4a4d;
    --watermark: #e6eef6;
    --paper: #ffffff;
    --backdrop: #e4e4e4;
    --ink: #3a3a3a;
  }
  * { margin: 0; padding: 0; box-sizing: border-box; }
  html, body {
    width: 1200px; height: 1200px; overflow: hidden;
    background: var(--backdrop);
    font-family: "Open Sans", Arial, sans-serif;
  }
  .letterhead {
    position: absolute;
    left: 211px; top: 50px;
    width: 778px; height: 1100px;
    background: var(--paper);
    overflow: hidden;
    box-shadow: 0 6px 24px rgba(0,0,0,0.12);
  }
  .brand {
    position: absolute;
    left: 52px; top: 58px;
    display: flex; align-items: center; gap: 14px;
  }
  .brand-dot {
    width: 46px; height: 46px;
    border: 4px solid var(--brand-blue);
    border-radius: 50%;
  }
  .brand-rule {
    width: 1.5px; height: 50px;
    background: var(--brand-blue);
  }
  .brand-name {
    color: var(--brand-blue);
    font-weight: 700;
    font-size: 22px;
    line-height: 1.05;
    letter-spacing: 3px;
    text-transform: uppercase;
  }
  .contact {
    position: absolute;
    right: 52px; top: 58px;
    font-size: 10.5px;
    line-height: 1.5;
    color: var(--ink);
    font-style: normal;
  }
  .contact .label { color: var(--brand-blue); }
  .decor {
    position: absolute; left: 0; top: 0;
    width: 778px; height: 1100px;
  }
  .website {
    position: absolute;
    right: 44px; top: 1040px;
    color: #fff;
    font-size: 15px;
    line-height: 20px;
    letter-spacing: 0.3px;
    white-space: nowrap;
  }
</style>
</head>
<body>
  <main class="letterhead">
    <svg class="decor" viewBox="0 0 778 1100" aria-hidden="true">
      <circle class="watermark-ring" cx="630" cy="830" r="135" fill="none" stroke="var(--watermark)" stroke-width="16"/>
      <path class="footer-stripe-grey" d="M0 1058 L400 1058 Q420 1058 428 1040 L433 1040 Q425 1066 400 1066 L0 1066 Z" fill="var(--brand-grey)"/>
      <path class="footer-band-blue" d="M0 1078 L420 1078 Q440 1078 448 1050 Q456 1010 490 1010 L778 1010 L778 1100 L0 1100 Z" fill="var(--brand-blue)"/>
    </svg>

    <header class="brand">
      <span class="brand-dot"></span>
      <span class="brand-rule"></span>
      <span class="brand-name">Northgate<br>Exteriors</span>
    </header>

    <address class="contact">
      215 Harbor View Rd Ste 300,<br>
      Millbrook, MD 20911<br>
      <span class="label">Phone:</span> 301-555-0148<br>
      <span class="label">Fax:</span> 301-555-0192
    </address>

    <div class="website">www.northgateexteriors.com</div>
  </main>
</body>
</html>
```